New Webpage for High Class Expert Witness Services Company

We are looking for a minimalist design for a webpage that just has our logo and an entry form offer to connect with one of our Liaisons.
The entry form should just ask for Name, Email, Contact Info and Description of Project.

Company Name is: The Marlowe Crest Advisory Services

Number of Pages Required

1 page

```html
<!DOCTYPE html>
<html lang="en">
<head>
<meta charset="utf-8">
<title>Marlowe Crest Advisory Services – Landing Page Variations</title>
<link rel="stylesheet" href="https://fonts.googleapis.com/css2?family=Cinzel:wght@400;500&family=Inter:wght@400;500&display=swap">
<style>
  :root{
    --sheet:#ffffff;
    --dark-1:#202020;
    --dark-2:#111111;
    --grey-1:#3c3c3c;
    --grey-2:#262626;
    --silver-1:#f1f1f1;
    --silver-2:#9d9d9d;
    --light-1:#ececec;
    --light-2:#d6d6d6;
    --ink-light:#d9d9d9;
    --ink-muted:#6f6f6f;
    --ink-dark:#2a2a2a;
    --ink-dark-muted:#7a7a7a;
    --line-dark:rgba(255,255,255,.14);
    --line-light:rgba(0,0,0,.12);
    --gold:linear-gradient(90deg,#9c7428 0%,#e6cb78 38%,#c59f4a 62%,#f0da8e 82%,#a9822f 100%);
    --gold-pale:linear-gradient(90deg,#f6ead0 0%,#d8bd7a 45%,#fbf0d3 65%,#b99548 100%);
    --silver:linear-gradient(90deg,#b4b4b4 0%,#f3f3f3 50%,#a2a2a2 100%);
    --gold-text:#d9aa45;
    --black:#151515;
  }
  *{box-sizing:border-box;margin:0;padding:0}
  html,body{width:1200px;height:1036px;overflow:hidden;background:var(--sheet)}
  body{position:relative;font-family:'Inter',sans-serif}

  .panel{position:absolute;width:349px;height:218px;overflow:hidden;color:var(--ink-light);
    background:radial-gradient(ellipse at 45% 35%,var(--dark-1) 0%,var(--dark-2) 75%)}
  .panel--grey{background:radial-gradient(ellipse at 45% 35%,var(--grey-1) 0%,var(--grey-2) 80%)}
  .panel--silver{color:var(--ink-dark);background:linear-gradient(120deg,var(--silver-1) 0%,#d2d2d2 30%,var(--silver-2) 55%,#e4e4e4 78%,var(--silver-1) 100%)}
  .panel--light{color:var(--ink-dark);background:linear-gradient(135deg,var(--light-1) 0%,#f4f4f4 40%,var(--light-2) 100%)}

  .backdrop{position:absolute;left:90px;top:32px;width:200px;height:165px;
    background:
      linear-gradient(115deg,rgba(255,255,255,0) 0%,rgba(255,255,255,.07) 30%,rgba(255,255,255,0) 31%,rgba(255,255,255,0) 55%,rgba(255,255,255,.05) 56%,rgba(255,255,255,0) 80%),
      linear-gradient(200deg,rgba(255,255,255,.06) 0%,rgba(255,255,255,0) 45%),
      radial-gradient(ellipse at 50% 35%,rgba(255,255,255,.08) 0%,rgba(255,255,255,0) 70%)}
  .panel--silver .backdrop,.panel--light .backdrop{background:
      linear-gradient(115deg,rgba(255,255,255,0) 0%,rgba(255,255,255,.45) 30%,rgba(255,255,255,0) 31%,rgba(255,255,255,0) 55%,rgba(0,0,0,.04) 56%,rgba(255,255,255,0) 80%),
      radial-gradient(ellipse at 50% 35%,rgba(255,255,255,.5) 0%,rgba(255,255,255,0) 70%)}

  .brand{position:absolute;left:39px;top:13px;display:flex;align-items:center;gap:5px;
    font-family:'Cinzel',serif;font-weight:400;font-size:8px;line-height:8.5px;letter-spacing:.3px;color:#e6e6e6;white-space:nowrap}
  .panel--silver .brand,.panel--light .brand{color:var(--ink-dark)}
  .brand__square{width:10px;height:10px;background:currentColor;flex:none}

  .phone{position:absolute;right:31px;top:12px;font-family:'Cinzel',serif;font-size:8.5px;letter-spacing:.2px;color:#e8e8e8;white-space:nowrap}
  .phone--large{font-size:10.5px;top:11px;right:33px}
  .phone--gold{color:var(--gold-text);font-size:9.5px}
  .panel--silver .phone,.panel--light .phone{color:var(--ink-dark)}

  .intro{position:absolute;left:39px;top:79px}
  .intro__label{font-family:'Cinzel',serif;font-size:4.8px;letter-spacing:.5px;color:var(--ink-muted);margin-bottom:5px;white-space:nowrap}
  .intro__headline{font-family:'Cinzel',serif;font-weight:400;font-size:13px;line-height:17px;letter-spacing:.4px;color:#cfcfcf;white-space:nowrap}
  .intro--stacked{top:79px}
  .panel--silver .intro__headline,.panel--light .intro__headline{color:var(--ink-dark)}
  .panel--silver .intro__label,.panel--light .intro__label{color:var(--ink-dark-muted)}

  .liaison-form{position:absolute;left:210px;top:36px;width:111px;height:128px;padding:11px 11px 0 13px;
    border:1px solid var(--line-dark);background:linear-gradient(160deg,rgba(255,255,255,.04),rgba(0,0,0,.15));
    display:flex;flex-direction:column}
  .liaison-form--tall{height:149px}
  .liaison-form--dark{background:linear-gradient(160deg,#1b1b1b,#3a3a3a);border-color:#555}
  .liaison-form--white{background:rgba(255,255,255,.75);border-color:var(--line-light)}
  .liaison-form__title{font-family:'Cinzel',serif;font-size:5.6px;letter-spacing:0;color:#dcdcdc;margin-bottom:8px;white-space:nowrap}
  .liaison-form--white .liaison-form__title{color:var(--ink-dark)}
  .field{height:11px;border:1px solid rgba(255,255,255,.3);margin-bottom:5px;padding:2px 4px;width:87px;
    font-size:3.6px;line-height:6px;color:#cfcfcf;white-space:nowrap}
  .field--area{height:26px}
  .liaison-form--white .field{border-color:rgba(0,0,0,.25);color:#333}
  .submit{height:12.5px;width:87px;display:flex;align-items:center;justify-content:center;
    font-family:'Cinzel',serif;font-weight:500;font-size:4.4px;letter-spacing:.4px;color:#1b1b1b}
  .submit--gold{background:var(--gold)}
  .submit--pale{background:var(--gold-pale)}
  .submit--silver{background:var(--silver)}
  .submit--black{background:var(--black);color:#fff}
  .liaison-form__or{font-size:3.4px;text-align:center;width:87px;margin-top:3px;color:#bbb}
  .liaison-form__phone{font-family:'Cinzel',serif;font-size:9.5px;text-align:center;width:87px;margin-top:3px;color:#e2e2e2}

  .footer{position:absolute;left:0;right:0;top:199px;bottom:0;border-top:1px solid var(--line-dark);
    font-size:3.2px;color:#8d8d8d;text-align:center;padding-top:7px}
  .panel--silver .footer,.panel--light .footer{border-top-color:var(--line-light);color:#555}
</style>
</head>
<body>

<!-- Row 1 -->
<section class="panel" style="left:46px;top:41px">
  <div class="backdrop" role="img" aria-label="Faint faceted shading behind the headline"></div>
  <div class="brand"><span class="brand__square"></span><span>Marlowe Crest<br>Advisory Services</span></div>
  <div class="phone">800-555-0142</div>
  <div class="intro"><p class="intro__label">MARLOWE CREST ADVISORY SERVICES</p><h1 class="intro__headline">SEAMLESS MEDICAL<br>EXPERT INTEGRATION</h1></div>
  <form class="liaison-form"><p class="liaison-form__title">CONNECT WITH A LIAISON</p><div class="field">Name*</div><div class="field">Email*</div><div class="field">Phone number*</div><div class="field field--area">Description of Project</div><div class="submit submit--gold">SUBMIT</div></form>
  <footer class="footer">© 2026 Marlowe Crest Advisory Services. All Rights Reserved</footer>
</section>

<section class="panel" style="left:435px;top:41px">
  <div class="backdrop" role="img" aria-label="Faint faceted shading behind the headline"></div>
  <div class="brand"><span class="brand__square"></span><span>Marlowe Crest<br>Advisory Services</span></div>
  <div class="phone">CALL US 800-555-0142</div>
  <div class="intro"><p class="intro__label">MARLOWE CREST ADVISORY SERVICES</p><h1 class="intro__headline">SEAMLESS MEDICAL<br>EXPERT INTEGRATION</h1></div>
  <form class="liaison-form"><p class="liaison-form__title">CONNECT WITH A LIAISON</p><div class="field">Name*</div><div class="field">Email*</div><div class="field">Phone number*</div><div class="field field--area">Description of Project</div><div class="submit submit--gold">SUBMIT</div></form>
  <footer class="footer">© 2026 Marlowe Crest Advisory Services. All Rights Reserved</footer>
</section>

<section class="panel panel--grey" style="left:814px;top:41px">
  <div class="backdrop" role="img" aria-label="Faint faceted shading behind the headline"></div>
  <div class="brand"><span class="brand__square"></span><span>Marlowe Crest<br>Advisory Services</span></div>
  <div class="phone">CALL US 800-555-0142</div>
  <div class="intro intro--stacked"><p class="intro__label">MARLOWE CREST ADVISORY SERVICES</p><h1 class="intro__headline">SEAMLESS<br>MEDICAL EXPERT<br>INTEGRATION</h1></div>
  <form class="liaison-form"><p class="liaison-form__title">CONNECT WITH A LIAISON</p><div class="field">Name*</div><div class="field">Email*</div><div class="field">Phone number*</div><div class="field field--area">Description of Project</div><div class="submit submit--silver">SUBMIT</div></form>
  <footer class="footer">© 2026 Marlowe Crest Advisory Services. All Rights Reserved</footer>
</section>

<!-- Row 2 -->
<section class="panel" style="left:46px;top:292px">
  <div class="backdrop" role="img" aria-label="Faint faceted shading behind the headline"></div>
  <div class="brand"><span class="brand__square"></span><span>Marlowe Crest<br>Advisory Services</span></div>
  <div class="intro"><p class="intro__label">MARLOWE CREST ADVISORY SERVICES</p><h1 class="intro__headline">SEAMLESS MEDICAL<br>EXPERT INTEGRATION</h1></div>
  <form class="liaison-form liaison-form--tall"><p class="liaison-form__title">CONNECT WITH A LIAISON</p><div class="field">Name*</div><div class="field">Email*</div><div class="field">Phone number*</div><div class="field field--area">Description of Project</div><div class="submit submit--gold">SUBMIT</div><p class="liaison-form__or">or</p><p class="liaison-form__phone">800-555-0142</p></form>
  <footer class="footer">© 2026 Marlowe Crest Advisory Services. All Rights Reserved</footer>
</section>

<section class="panel" style="left:435px;top:292px">
  <div class="backdrop" role="img" aria-label="Faint faceted shading behind the headline"></div>
  <div class="brand"><span class="brand__square"></span><span>Marlowe Crest<br>Advisory Services</span></div>
  <div class="phone phone--gold">800-555-0142</div>
  <div class="intro"><p class="intro__label">MARLOWE CREST ADVISORY SERVICES</p><h1 class="intro__headline">SEAMLESS MEDICAL<br>EXPERT INTEGRATION</h1></div>
  <form class="liaison-form" style="top:36px"><p class="liaison-form__title">CONNECT WITH A LIAISON</p><div class="field">Name*</div><div class="field">Email*</div><div class="field">Phone number*</div><div class="field field--area">Description of Project</div><div class="submit submit--gold">SUBMIT</div></form>
  <footer class="footer">© 2026 Marlowe Crest Advisory Services. All Rights Reserved</footer>
</section>

<section class="panel panel--silver" style="left:817px;top:294px">
  <div class="backdrop" role="img" aria-label="Faint faceted shading behind the headline"></div>
  <div class="brand"><span class="brand__square"></span><span>Marlowe Crest<br>Advisory Services</span></div>
  <div class="phone">CALL US 800-555-0142</div>
  <div class="intro intro--stacked"><p class="intro__label">MARLOWE CREST ADVISORY SERVICES</p><h1 class="intro__headline">SEAMLESS<br>MEDICAL EXPERT<br>INTEGRATION</h1></div>
  <form class="liaison-form liaison-form--dark"><p class="liaison-form__title">CONNECT WITH A LIAISON</p><div class="field">Name*</div><div class="field">Email*</div><div class="field">Phone number*</div><div class="field field--area">Description of Project</div><div class="submit submit--silver">SUBMIT</div></form>
  <footer class="footer">© 2026 Marlowe Crest Advisory Services. All Rights Reserved</footer>
</section>

<!-- Row 3 -->
<section class="panel" style="left:46px;top:543px">
  <div class="backdrop" role="img" aria-label="Faint faceted shading behind the headline"></div>
  <div class="brand"><span class="brand__square"></span><span>Marlowe Crest<br>Advisory Services</span></div>
  <div class="phone phone--large">800-555-0142</div>
  <div class="intro"><p class="intro__label">MARLOWE CREST ADVISORY SERVICES</p><h1 class="intro__headline">SEAMLESS MEDICAL<br>EXPERT INTEGRATION</h1></div>
  <form class="liaison-form"><p class="liaison-form__title">CONNECT WITH A LIAISON</p><div class="field">Name*</div><div class="field">Email*</div><div class="field">Phone number*</div><div class="field field--area">Description of Project</div><div class="submit submit--pale">SUBMIT</div></form>
  <footer class="footer">© 2026 Marlowe Crest Advisory Services. All Rights Reserved</footer>
</section>

<section class="panel" style="left:435px;top:543px">
  <div class="backdrop" role="img" aria-label="Faint faceted shading behind the headline"></div>
  <div class="brand"><span class="brand__square"></span><span>Marlowe Crest<br>Advisory Services</span></div>
  <div class="phone phone--large" style="color:#bdbdbd">800-555-0142</div>
  <div class="intro"><p class="intro__label">MARLOWE CREST ADVISORY SERVICES</p><h1 class="intro__headline">SEAMLESS MEDICAL<br>EXPERT INTEGRATION</h1></div>
  <form class="liaison-form"><p class="liaison-form__title">CONNECT WITH A LIAISON</p><div class="field">Name*</div><div class="field">Email*</div><div class="field">Phone number*</div><div class="field field--area">Description of Project</div><div class="submit submit--gold">SUBMIT</div></form>
  <footer class="footer">© 2026 Marlowe Crest Advisory Services. All Rights Reserved</footer>
</section>

<section class="panel panel--light" style="left:814px;top:542px">
  <div class="backdrop" role="img" aria-label="Faint faceted shading behind the headline"></div>
  <div class="brand"><span class="brand__square"></span><span>Marlowe Crest<br>Advisory Services</span></div>
  <div class="phone">CALL 800-555-0142</div>
  <div class="intro intro--stacked"><p class="intro__label">MARLOWE CREST ADVISORY SERVICES</p><h1 class="intro__headline">SEAMLESS<br>MEDICAL EXPERT<br>INTEGRATION</h1></div>
  <form class="liaison-form liaison-form--white"><p class="liaison-form__title">CONNECT WITH A LIAISON</p><div class="field">Name*</div><div class="field">Email*</div><div class="field">Phone number*</div><div class="field field--area">Description of Project</div><div class="submit submit--black">SUBMIT</div></form>
  <footer class="footer">© 2026 Marlowe Crest Advisory Services. All Rights Reserved</footer>
</section>

<!-- Row 4 -->
<section class="panel" style="left:46px;top:771px">
  <div class="backdrop" role="img" aria-label="Faint faceted shading behind the headline"></div>
  <div class="brand"><span class="brand__square"></span><span>Marlowe Crest<br>Advisory Services</span></div>
  <div class="phone phone--large">800-555-0142</div>
  <div class="intro"><p class="intro__label">MARLOWE CREST ADVISORY SERVICES</p><h1 class="intro__headline">SEAMLESS MEDICAL<br>EXPERT INTEGRATION</h1></div>
  <form class="liaison-form"><p class="liaison-form__title">CONNECT WITH A LIAISON</p><div class="field">Name*</div><div class="field">Email*</div><div class="field">Phone number*</div><div class="field field--area">Description of Project</div><div class="submit submit--gold">SUBMIT</div></form>
  <footer class="footer">© 2026 Marlowe Crest Advisory Services. All Rights Reserved</footer>
</section>

<section class="panel panel--grey" style="left:437px;top:778px">
  <div class="backdrop" role="img" aria-label="Faint faceted shading behind the headline"></div>
  <div class="brand"><span class="brand__square"></span><span>Marlowe Crest<br>Advisory Services</span></div>
  <div class="phone" style="font-size:10px">800-555-0142</div>
  <div class="intro"><p class="intro__label">MARLOWE CREST ADVISORY SERVICES</p><h1 class="intro__headline">SEAMLESS MEDICAL<br>EXPERT INTEGRATION</h1></div>
  <form class="liaison-form"><p class="liaison-form__title">CONNECT WITH A LIAISON</p><div class="field">Name*</div><div class="field">Email*</div><div class="field">Phone number*</div><div class="field field--area">Description of Project</div><div class="submit submit--gold">SUBMIT</div></form>
  <footer class="footer">© 2026 Marlowe Crest Advisory Services. All Rights Reserved</footer>
</section>

</body>
</html>
```